Web portal for events

The project is about creating a web application - portal for culture events in Denmark.

Design

We aim for very simplistic, light and fully responsive design. The white background is preferable, as well as light color tones. As inspirational points we like the colors used in www.parvolio.com and www.brindlemoor.org

FORMAT AND REQUIREMENTS:
1. Design should be provided based on the wireframes specified as a link below.
2. The design (and all of its pages) should be provided in three resolution variants:
- Desktop
- Tablet
- Phone
3. The design should be provided as PSD, where each page/section should be in its own PSD file
4. All graphical elements in the design should be delivered as single layers which can then be extracted from the PSD.
5. All graphical elements (icons, graphical buttons, etc.) should be provided as vector objects in the PSD, so that they can be exported into different sizes without loss of quality (for responsiveness)
6. The design should use either web safe fonts or Google Fonts.

RESPONSIVENESS
The web application should be visible on any devices (i.e. responsive design)

WIREFRAMES:
https://velkotrams.examplewire.com/projects/fennoplex/prototype/Homepage?key=3b7c19d0f2a84e6c5d1e9a07b4f2c8d6e1a3f590

We expect design of the following wireframes:

Homepage:
https://velkotrams.examplewire.com/projects/fennoplex/Homepage

For arrangører - billede uploaded:
https://velkotrams.examplewire.com/projects/fennoplex/For%20arrang%C3%B8rer%20-%20billede%20uploaded

Further specifications of the project (i.e. functionality, etc.):
https://files.quorvane.net/document/d/8pKw_Rt2mZqLx4NvB7yHc0aEs9uGdJf3TiOb6nVlW1k/edit?usp=sharing

```html
<!DOCTYPE html>
<html lang="da">
<head>
<meta charset="utf-8">
<title>KULTRO – Din guide til kultur og events</title>
<link href="https://fonts.googleapis.com/css2?family=Source+Sans+3:wght@400;600;700&family=Montserrat:wght@800;900&display=swap" rel="stylesheet">
<style>
:root{
  --navy:#0b0c33;
  --orange:#e0401a;
  --orange-dark:#c8340f;
  --slate:#3b4350;
  --grey-btn:#b9bcc1;
  --nav-bg:#eeeeee;
  --line:#dcdcdc;
  --text:#333;
  --muted:#666;
  --footer:#2d2d2d;
  --footer-low:#262626;
}
*{box-sizing:border-box;margin:0;padding:0}
html,body{width:762px;height:1200px;overflow:hidden}
body{font-family:"Source Sans 3",Arial,sans-serif;color:var(--text);background:#fff;position:relative}
.site-header{height:70px;background:var(--navy);position:relative}
.brand{position:absolute;left:83px;top:14px;color:#fff}
.brand-name{font-size:31px;font-weight:400;letter-spacing:1px;line-height:1}
.brand-tag{font-size:8px;margin-top:3px}
.search{position:absolute;left:270px;top:22px;width:193px;height:27px;background:#fff;display:flex;align-items:center;padding:0 10px;font-size:10px;color:#888;justify-content:space-between}
.adv{position:absolute;left:476px;top:30px;font-size:8px;color:#fff;text-decoration:underline}
.btn-login,.btn-signup{position:absolute;top:23px;height:23px;width:56px;border-radius:3px;color:#fff;font-size:9px;display:flex;align-items:center;justify-content:center}
.btn-login{left:553px;background:var(--orange)}
.btn-signup{left:623px;background:#4a4f5a}
.main-nav{height:42px;background:var(--nav-bg);display:flex;padding-left:83px}
.main-nav a{display:flex;align-items:center;justify-content:center;font-size:9px;font-weight:600;color:#333;text-decoration:none;border-left:1px solid #d5d5d5;height:100%}
.main-nav a:last-child{border-right:1px solid #d5d5d5}
.hero{height:262px;position:relative;background:linear-gradient(90deg,#0c0b32 0%,#18173f 45%,#3a3355 70%,#231e45 100%);overflow:hidden}
.hero-photo{position:absolute;left:330px;top:0;width:432px;height:262px;background:radial-gradient(circle at 45% 45%,#3fa59a 0%,#2a5a70 25%,#4a3f66 50%,rgba(35,30,69,0) 75%)}
.hero-title{position:absolute;left:83px;top:96px;font-family:Montserrat,Arial,sans-serif;color:#fff}
.hero-title .l1{font-size:23px;font-weight:800;letter-spacing:.5px}
.hero-title .l2{font-size:41px;font-weight:900;line-height:1;margin-top:2px}
.hero-title .l2 span{color:var(--orange)}
.hero-arrow{position:absolute;top:102px}
.content{position:absolute;left:83px;top:374px;width:393px}
.section-head{display:flex;align-items:center;height:54px;border-bottom:1px solid var(--line);margin-bottom:10px}
.section-head h2{font-size:12px;font-weight:700;color:#111;width:122px}
.sort{font-size:9px;color:#333;margin-right:8px}
.chip{height:17px;font-size:8px;color:#fff;display:flex;align-items:center;justify-content:center;margin-right:8px;width:45px}
.chip.dark{background:var(--navy)}
.chip.red{background:var(--orange)}
.grid{display:grid;grid-template-columns:repeat(3,122px);column-gap:14px;row-gap:15px}
.card{border:1px solid var(--line);height:131px}
.card-img{height:62px}
.card h3{font-size:9.5px;font-weight:400;color:#555;margin:8px 5px 3px}
.card-meta{display:flex;justify-content:space-between;font-size:6.5px;color:#333;margin:0 7px 0 5px}
.card-actions{display:flex;gap:5px;margin:9px 7px 0 8px}
.card-actions span{flex:1;height:16px;border-radius:8px;font-size:6.5px;color:#fff;display:flex;align-items:center;justify-content:center}
.see{background:var(--grey-btn)}
.see.active{background:var(--orange)}
.fav{background:var(--slate)}
.pager{position:absolute;left:103px;top:1021px;display:flex;align-items:center}
.pager span{width:16px;height:16px;border-radius:50%;background:#a9adb3;color:#fff;font-size:7px;display:flex;align-items:center;justify-content:center;margin-right:3px}
.pager span.on{background:var(--orange)}
.pager .dots{width:100px;border-top:1px dotted #999;margin:0 4px 0 2px}
.side-box{position:absolute;left:501px;width:178px;border:1px solid var(--line);background:#fff;box-shadow:0 0 2px rgba(0,0,0,.08)}
.side-box h2{font-size:12px;font-weight:700;color:var(--orange);text-align:center;padding:9px 0 7px;border-bottom:1px dotted #bbb;margin:0 7px}
.favs{top:392px;height:308px}
.fav-item{display:flex;margin:0 9px;padding:13px 0;border-bottom:1px solid #eee}
.fav-thumb{width:52px;height:45px;flex:none;margin-right:9px}
.fav-item h4{font-size:9px;font-weight:400;color:#222;margin-bottom:2px}
.fav-item p{font-size:7px;line-height:13px;color:#555}
.btn-more{display:flex;width:89px;height:25px;margin:18px auto 0;background:var(--navy);border-radius:4px;color:#fff;font-size:11px;font-weight:600;align-items:center;justify-content:center}
.news{top:718px;height:192px}
.news p{font-size:7px;line-height:12.5px;color:#333;margin:10px 11px 0;text-align:justify}
.email{margin:14px 12px 0;height:23px;border:1px solid #ccc;font-size:7px;color:#aaa;padding:7px 9px}
.btn-send{display:flex;width:82px;height:24px;margin:12px auto 0;background:var(--orange);border-radius:4px;color:#fff;font-size:11px;align-items:center;justify-content:center}
.site-footer{position:absolute;left:0;top:1058px;width:762px;height:142px;background:var(--footer)}
.social{display:flex;padding:20px 0 0 83px;height:79px;border-bottom:1px solid #3a3a3a}
.social-item{display:flex;width:210px}
.social-mark{width:37px;height:37px;border-radius:4px;margin-right:22px;flex:none}
.social-item h3{color:#fff;font-size:12.5px;font-weight:400;margin-bottom:3px}
.social-item p{color:#bbb;font-size:7.5px;line-height:11px}
.footer-links{text-align:center;color:#fff;font-size:7.5px;margin-top:16px}
.copyright{text-align:center;color:#bbb;font-size:7px;margin-top:10px}
</style>
</head>
<body>
<header class="site-header">
  <div class="brand"><div class="brand-name">KULTRO</div><div class="brand-tag">Din guide til kultur og events</div></div>
  <div class="search">Search
    <svg width="10" height="10" viewBox="0 0 10 10"><circle cx="4" cy="4" r="3" fill="none" stroke="#444" stroke-width="1.3"/><line x1="6.2" y1="6.2" x2="9.2" y2="9.2" stroke="#444" stroke-width="1.5"/></svg>
  </div>
  <span class="adv">Advanced search</span>
  <span class="btn-login">LOGIN</span>
  <span class="btn-signup">SIGNUP</span>
</header>
<nav class="main-nav">
  <a style="width:55px">ALLE</a><a style="width:60px">MUSIK</a><a style="width:63px">SPORT</a><a style="width:60px">TEATER</a><a style="width:76px">UDSTILLING</a><a style="width:67px">AELDRE</a><a style="width:65px">BORN</a><a style="width:66px">MOTION</a><a style="width:80px">DIVERSE</a>
</nav>
<section class="hero">
  <div class="hero-photo" role="img" aria-label="Photo of a DJ holding a vinyl record in front of a wall of records"></div>
  <div class="hero-title"><div class="l1">OUR CULTURAL EVENTS</div><div class="l2">IN <span>DENMARK</span></div></div>
  <svg class="hero-arrow" style="left:14px" width="30" height="58" viewBox="0 0 30 58"><polyline points="29,1 1,29 29,57" fill="none" stroke="#fff" stroke-width="1.5"/></svg>
  <svg class="hero-arrow" style="left:714px" width="30" height="58" viewBox="0 0 30 58"><polyline points="1,1 29,29 1,57" fill="none" stroke="#fff" stroke-width="1.5"/></svg>
</section>

<main class="content">
  <div class="section-head">
    <h2>POPULAR EVENTS</h2><span class="sort">Sorter efter</span>
    <span class="chip dark">Popular</span><span class="chip red">Order ▾</span><span class="chip red">Dato</span><span class="chip red">Pris</span>
  </div>
  <div class="grid">
    <article class="card"><div class="card-img" style="background:linear-gradient(#6a7d8a,#4a4a3a)" role="img" aria-label="Musicians performing outdoors"></div><h3>Jens Holmer koncer</h3><div class="card-meta"><span>Oplev xxxx.....................</span><span>2.8.2014</span></div><div class="card-actions"><span class="see active">SE EVENT</span><span class="fav">FAVORITTER</span></div></article>
    <article class="card"><div class="card-img" style="background:linear-gradient(#c0321c,#3a1a18)" role="img" aria-label="Concert stage with red lights"></div><h3>Jens Holmer koncer</h3><div class="card-meta"><span>Oplev xxxx.....................</span><span>2.8.2014</span></div><div class="card-actions"><span class="see">SE EVENT</span><span class="fav">FAVORITTER</span></div></article>
    <article class="card"><div class="card-img" style="background:linear-gradient(135deg,#c83a2e,#3f8a3c,#d8c24a)" role="img" aria-label="Colourful parade performers"></div><h3>Jens Holmer koncer</h3><div class="card-meta"><span>Oplev xxxx.....................</span><span>2.8.2014</span></div><div class="card-actions"><span class="see">SE EVENT</span><span class="fav">FAVORITTER</span></div></article>
    <article class="card"><div class="card-img" style="background:linear-gradient(#b8231c,#5a3a3a)" role="img" aria-label="Band on a red-lit stage"></div><h3>Jens Holmer koncer</h3><div class="card-meta"><span>Oplev xxxx.....................</span><span>2.8.2014</span></div><div class="card-actions"><span class="see">SE EVENT</span><span class="fav">FAVORITTER</span></div></article>
    <article class="card"><div class="card-img" style="background:linear-gradient(#8a8a8a,#4a4a4a)" role="img" aria-label="Large concert crowd"></div><h3>Jens Holmer koncer</h3><div class="card-meta"><span>Oplev xxxx.....................</span><span>2.8.2014</span></div><div class="card-actions"><span class="see">SE EVENT</span><span class="fav">FAVORITTER</span></div></article>
    <article class="card"><div class="card-img" style="background:linear-gradient(#4a3a34,#2a2422)" role="img" aria-label="Band on a dim stage"></div><h3>Jens Holmer koncer</h3><div class="card-meta"><span>Oplev xxxx.....................</span><span>2.8.2014</span></div><div class="card-actions"><span class="see">SE EVENT</span><span class="fav">FAVORITTER</span></div></article>
    <article class="card"><div class="card-img" style="background:linear-gradient(#2a1a14,#6a3a2a)" role="img" aria-label="Singer at a microphone"></div><h3>Jens Holmer koncer</h3><div class="card-meta"><span>Oplev xxxx.....................</span><span>2.8.2014</span></div><div class="card-actions"><span class="see">SE EVENT</span><span class="fav">FAVORITTER</span></div></article>
    <article class="card"><div class="card-img" style="background:linear-gradient(#5a6070,#2a2a30)" role="img" aria-label="Guitarist performing"></div><h3>Jens Holmer koncer</h3><div class="card-meta"><span>Oplev xxxx.....................</span><span>2.8.2014</span></div><div class="card-actions"><span class="see">SE EVENT</span><span class="fav">FAVORITTER</span></div></article>
    <article class="card"><div class="card-img" style="background:linear-gradient(#3a4a8a,#8a5a4a)" role="img" aria-label="Rock band on stage with banner"></div><h3>Jens Holmer koncer</h3><div class="card-meta"><span>Oplev xxxx.....................</span><span>2.8.2014</span></div><div class="card-actions"><span class="see">SE EVENT</span><span class="fav">FAVORITTER</span></div></article>
    <article class="card"><div class="card-img" style="background:linear-gradient(#b8231c,#5a3a3a)" role="img" aria-label="Band on a red-lit stage"></div><h3>Jens Holmer koncer</h3><div class="card-meta"><span>Oplev xxxx.....................</span><span>2.8.2014</span></div><div class="card-actions"><span class="see">SE EVENT</span><span class="fav">FAVORITTER</span></div></article>
    <article class="card"><div class="card-img" style="background:linear-gradient(135deg,#8a8a1a,#2a2a14)" role="img" aria-label="Guitarist under yellow light"></div><h3>Jens Holmer koncer</h3><div class="card-meta"><span>Oplev xxxx.....................</span><span>2.8.2014</span></div><div class="card-actions"><span class="see">SE EVENT</span><span class="fav">FAVORITTER</span></div></article>
    <article class="card"><div class="card-img" style="background:linear-gradient(135deg,#5a1a14,#b8332a)" role="img" aria-label="Singer performing on stage"></div><h3>Jens Holmer koncer</h3><div class="card-meta"><span>Oplev xxxx.....................</span><span>2.8.2014</span></div><div class="card-actions"><span class="see">SE EVENT</span><span class="fav">FAVORITTER</span></div></article>
  </div>
</main>
<div class="pager"><span class="on">1</span><span>2</span><span>3</span><i class="dots"></i><span>24</span></div>

<aside class="side-box favs">
  <h2>MINE FAVORITTER</h2>
  <div class="fav-item"><div class="fav-thumb" style="background:linear-gradient(#2a2a2a,#555)" role="img" aria-label="Singer on stage"></div><div><h4>Consectetuer adipiscing</h4><p>Aenean commodo ligula eget dolor. Aenean massa. Cum sociis natoque penatibus</p></div></div>
  <div class="fav-item"><div class="fav-thumb" style="background:linear-gradient(135deg,#e0a0d0,#7a6ad0)" role="img" aria-label="Performer in colourful lights"></div><div><h4>Consectetuer adipiscing</h4><p>Aenean commodo ligula eget dolor. Aenean massa. Cum sociis natoque penatibus</p></div></div>
  <div class="fav-item" style="border-bottom:1px solid #eee"><div class="fav-thumb" style="background:linear-gradient(#4a5060,#22252a)" role="img" aria-label="Guitarist performing"></div><div><h4>Consectetuer adipiscing</h4><p>Aenean commodo ligula eget dolor. Aenean massa. Cum sociis natoque penatibus</p></div></div>
  <span class="btn-more">SEE MORE</span>
</aside>

<aside class="side-box news">
  <h2>NYHEDSBREV</h2>
  <p>Consectetuer adipiscing Aenean commodo ligula eget dolor. Aenean massa. Cum sociis natoque penatibus et magnis dis parturient montes, nascetur ridiculus mus. Donec quam felis, ultricies nec.</p>
  <div class="email">Email Address</div>
  <span class="btn-send">SEND</span>
</aside>

<footer class="site-footer">
  <div class="social">
    <div class="social-item"><span class="social-mark" style="background:#3b5a9a"></span><div><h3>Socialia</h3><p>Lorem ipsum dolor sit amet conse<br>ctetur adipiscing elit</p></div></div>
    <div class="social-item"><span class="social-mark" style="background:#27a9e1"></span><div><h3>Chirpnet</h3><p>Lorem ipsum dolor sit amet conse<br>ctetur adipiscing elit</p></div></div>
    <div class="social-item"><span class="social-mark" style="background:#d23a2a"></span><div><h3>Streamly</h3><p>Lorem ipsum dolor sit amet conse<br>ctetur adipiscing elit</p></div></div>
  </div>
  <div class="footer-links">Om Kultro | &nbsp;Vilkar &amp; betingelser &nbsp;| &nbsp;kobspolitik &nbsp;| &nbsp;Nyhedsbrev | Kontakt | Login/ Register | Help | For arrangoger</div>
  <div class="copyright">Copy right 2014 | All rights reserved</div>
</footer>
</body>
</html>
```